Stonebridge Building and Projects business cards

A business card with watermark background (construction work)

Company logo attached

Home improvement projects
House renovations
Bathroom and kitchen renovations
House extensions
New builds and granny flats

Director Omar Haddani
(Phone number)
omar@sbpbuilding.com.au
(Instagram logo) sbp_building

```html
<!DOCTYPE html>
<html lang="en">
<head>
<meta charset="utf-8">
<title>Stonebridge Building and Projects – Business Cards</title>
<link rel="stylesheet" href="https://fonts.googleapis.com/css2?family=Montserrat:wght@500;600;700&family=Arimo:wght@400&display=swap">
<style>
  :root {
    --bg: #0f0f10;
    --card: #242529;
    --card-edge: #2f78c4;
    --blue: #2f7cc9;
    --text-light: #e4e5e8;
    --text-soft: #b9bbc0;
    --rule: #4a4c52;
    --emboss: #4a4c51;
  }
  * { margin: 0; padding: 0; box-sizing: border-box; }
  html, body { width: 1200px; height: 820px; overflow: hidden; background: var(--bg); }
  .canvas {
    width: 1200px; height: 820px;
    display: flex; align-items: center; justify-content: center; gap: 40px;
  }
  .card {
    width: 540px; height: 310px;
    background: var(--card);
    border: 2px solid var(--card-edge);
    border-radius: 3px;
    position: relative;
    font-family: "Arimo", Arial, sans-serif;
  }

  /* Front */
  .brand {
    position: absolute; top: 44px; right: 40px; width: 330px; text-align: left;
  }
  .brand-mark { display: flex; align-items: center; gap: 10px; }
  .brand-square { width: 14px; height: 14px; background: var(--blue); flex: none; }
  .brand-name {
    font-family: "Montserrat", Arial, sans-serif; font-weight: 700;
    color: var(--blue); font-size: 22px; line-height: 1.15;
  }
  .brand-tagline {
    margin-top: 10px; padding-top: 6px; padding-left: 24px;
    border-top: 1px solid var(--blue);
    font-size: 13px; color: var(--blue); width: 220px;
  }
  .divider {
    position: absolute; left: 150px; right: 30px; top: 160px;
    height: 1px; background: var(--rule);
  }
  .contact { position: absolute; left: 34px; bottom: 28px; }
  .person-name {
    font-family: "Montserrat", Arial, sans-serif; font-weight: 700;
    color: var(--blue); font-size: 22px;
  }
  .person-role { color: var(--text-light); font-size: 14px; margin: 2px 0 12px; }
  .contact-list { list-style: none; color: var(--text-light); font-size: 13px; }
  .contact-list li { display: flex; align-items: center; gap: 8px; margin-top: 4px; }
  .contact-list svg { width: 13px; height: 13px; flex: none; }
  .web-accent { color: var(--blue); }
  .social {
    position: absolute; right: 30px; bottom: 70px;
    display: flex; align-items: center; gap: 8px;
    color: var(--text-soft); font-size: 13px;
  }
  .social-square { width: 12px; height: 12px; background: var(--blue); border-radius: 2px; }

  /* Back */
  .card-back { display: flex; flex-direction: column; align-items: center; justify-content: center; }
  .back-name {
    font-family: "Montserrat", Arial, sans-serif; font-weight: 700;
    color: var(--emboss); font-size: 34px; line-height: 1.1; text-align: center; width: 380px;
  }
  .services {
    margin-top: 26px; list-style: none; text-align: center;
    color: var(--text-light); font-size: 13px; line-height: 1.6;
  }
</style>
</head>
<body>
<main class="canvas">

  <section class="card card-front" aria-label="Business card front">
    <div class="brand">
      <div class="brand-mark">
        <span class="brand-square"></span>
        <span class="brand-name">Stonebridge Building and Projects</span>
      </div>
      <div class="brand-tagline">Built on solid ground!</div>
    </div>

    <div class="divider"></div>

    <div class="contact">
      <div class="person-name">Omar Haddani</div>
      <div class="person-role">Director</div>
      <ul class="contact-list">
        <li>
          <svg viewBox="0 0 16 16" aria-hidden="true"><path fill="#2f7cc9" d="M3.5 1.5l2.5 3-1.5 1.5c.8 2 2.5 3.7 4.5 4.5L10.5 9l3 2.5-1.5 2.5C6.5 14 2 9.5 1 3z"/></svg>
          044-870 215 364
        </li>
        <li>
          <svg viewBox="0 0 16 16" aria-hidden="true"><rect x="1" y="3" width="14" height="10" fill="#2f7cc9"/><path d="M1 3l7 6 7-6" fill="none" stroke="#242529" stroke-width="1.3"/></svg>
          omar@sbpbuilding.com.au
        </li>
        <li>
          <svg viewBox="0 0 16 16" aria-hidden="true"><g fill="none" stroke="#2f7cc9" stroke-width="1.3"><circle cx="8" cy="8" r="6.5"/><ellipse cx="8" cy="8" rx="3" ry="6.5"/><path d="M1.5 8h13M2.5 4.8h11M2.5 11.2h11"/></g></svg>
          <span>www.<span class="web-accent">sbpbuilding</span>.com.au</span>
        </li>
      </ul>
    </div>

    <div class="social">
      <span>sbp_building</span>
      <span class="social-square"></span>
    </div>
  </section>

  <section class="card card-back" aria-label="Business card back">
    <div class="back-name">Stonebridge Building and Projects</div>
    <ul class="services">
      <li>Home improvement projects | House renovations</li>
      <li>Bathroom and kitchen renovations</li>
      <li>House extensions | New builds and granny flats</li>
    </ul>
  </section>

</main>
</body>
</html>
```